SaaS Early tech startup business card design

Unique design for experience ecommerce platform company. the business cards will be used by executive members. conformance with color code is required.

```html
<!DOCTYPE html>
<html lang="en">
<head>
<meta charset="utf-8">
<title>vantly – Business Card</title>
<link rel="stylesheet" href="https://fonts.googleapis.com/css2?family=Inter:wght@400;500;700&family=Rubik:wght@700&display=swap">
<style>
  :root {
    --backdrop: #3b3c3e;
    --paper: #ffffff;
    --ink: #4a4a4a;
    --teal-deep: #0a6f92;
    --teal-mid: #05908f;
    --teal-bright: #04c2ae;
    --navy-fade: #05618a;
    --brand-front: #0b7a95;
    --brand-back: #0b3347;
    --white: #ffffff;
  }
  * { margin: 0; padding: 0; box-sizing: border-box; }
  html, body {
    width: 1200px; height: 1200px; overflow: hidden;
    background: var(--backdrop);
    font-family: "Inter", Arial, sans-serif;
  }
  .canvas { position: relative; width: 1200px; height: 1200px; }

  .card {
    position: absolute; left: 257px; width: 686px; height: 392px;
    overflow: hidden;
  }
  .card--front { top: 165px; background: var(--paper); }
  .card--back {
    top: 653px;
    background: linear-gradient(180deg, var(--teal-bright) 0%, #049fa5 45%, var(--navy-fade) 100%);
  }

  .name-banner { position: absolute; left: 0; top: 52px; width: 275px; height: 61px; }
  .name-banner svg { position: absolute; inset: 0; }
  .name-banner__text { position: absolute; left: 40px; top: 11px; color: var(--white); }
  .holder-name { font-size: 22px; font-weight: 700; letter-spacing: 0.3px; line-height: 1.1; }
  .holder-role { font-size: 15px; font-weight: 400; margin-top: 1px; }

  .brand-mark {
    position: absolute; font-family: "Rubik", "Inter", sans-serif; font-weight: 700;
    letter-spacing: -2px; line-height: 1;
  }
  .card--front .brand-mark { right: 42px; top: 40px; font-size: 82px; color: var(--brand-front); }
  .card--back .brand-mark {
    left: 0; right: 0; top: 120px; text-align: center;
    font-size: 150px; color: var(--brand-back);
  }

  .contact-list { position: absolute; left: 41px; top: 228px; list-style: none; }
  .contact-list li {
    display: flex; align-items: center; height: 20px; margin-bottom: 0.5px;
    font-size: 14.5px; color: var(--ink);
  }
  .contact-list svg { width: 14px; height: 14px; margin-right: 8px; fill: var(--teal-bright); }

  .address-band {
    position: absolute; left: 0; top: 325px; width: 100%; height: 25px;
    background: linear-gradient(90deg, var(--teal-deep) 0%, var(--teal-mid) 30%, var(--teal-bright) 55%, var(--teal-deep) 100%);
    color: var(--white); font-size: 15.5px; line-height: 25px; padding-left: 38px;
  }
</style>
</head>
<body>
<main class="canvas">
  <section class="card card--front">
    <div class="name-banner">
      <svg width="275" height="61" viewBox="0 0 275 61">
        <defs>
          <linearGradient id="bannerFill" x1="0" x2="1">
            <stop offset="0" stop-color="#0a6f92"/>
            <stop offset="1" stop-color="#05908f"/>
          </linearGradient>
        </defs>
        <path d="M0 0 H242 L275 57 Q277 61 272 61 H0 Z" fill="url(#bannerFill)"/>
      </svg>
      <div class="name-banner__text">
        <p class="holder-name">DANIEL REYES</p>
        <p class="holder-role">President</p>
      </div>
    </div>

    <p class="brand-mark">vantly</p>

    <ul class="contact-list">
      <li><svg viewBox="0 0 24 24"><path d="M6.6 10.8a15.1 15.1 0 0 0 6.6 6.6l2.2-2.2c.3-.3.7-.4 1-.2 1.1.4 2.3.6 3.6.6.6 0 1 .4 1 1V20c0 .6-.4 1-1 1A17 17 0 0 1 3 4c0-.6.4-1 1-1h3.5c.6 0 1 .4 1 1 0 1.3.2 2.5.6 3.6.1.3 0 .7-.2 1z"/></svg>555-214-0183</li>
      <li><svg viewBox="0 0 24 24"><path d="M7 1h10a2 2 0 0 1 2 2v18a2 2 0 0 1-2 2H7a2 2 0 0 1-2-2V3a2 2 0 0 1 2-2zm0 3v14h10V4zm5 15.5a1 1 0 1 0 0 2 1 1 0 0 0 0-2z"/></svg>555-318-4720</li>
      <li><svg viewBox="0 0 24 24"><path d="M2 6h20v12H2zm2 2v.4l8 5 8-5V8l-8 5z"/></svg>hello@vantly.com</li>
      <li><svg viewBox="0 0 24 24"><circle cx="12" cy="12" r="10"/></svg>www.vantly.com</li>
    </ul>

    <div class="address-band">2218 Willow Crest Drive, Fairbanks, Alaska 99701</div>
  </section>

  <section class="card card--back">
    <p class="brand-mark">vantly</p>
  </section>
</main>
</body>
</html>
```